Business Card Design for a Personal Trainer

I need a business card design for my job as a personal trainer. It should have a unique, modern and exclusive design. On the front there should be only my logo with my name and my job. 0162/3819204 Tobias Lendhart Wiesengrundweg 14 80417 Munich Germany The most important contact information is the web adress. it can be bigger than the rest, but its not necessary. The card should be 8,5cmx5,5cm big. Font: Roboto. Colors: black, white, gray, 56c1ff.

```html
<!DOCTYPE html>
<html lang="de">
<head>
<meta charset="utf-8">
<title>Tobias Lendhart – Visitenkarte</title>
<link rel="stylesheet" href="https://fonts.googleapis.com/css2?family=Work+Sans:wght@400;500;600&display=swap">
<style>
  :root {
    --stage: #3a3230;
    --card-white: #ffffff;
    --ink: #1c1c1c;
    --ink-soft: #333333;
    --rule: #222222;
    --photo-deep: #15161f;
    --photo-mid: #3c3f58;
    --photo-mist: #8a8ea6;
    --on-photo: #ffffff;
  }
  * { box-sizing: border-box; margin: 0; padding: 0; }
  html, body { width: 1200px; height: 715px; overflow: hidden; }
  body {
    background: var(--stage);
    font-family: "Work Sans", Roboto, sans-serif;
    position: relative;
  }
  .card {
    position: absolute;
    top: 190px;
    width: 520px;
    height: 336px;
    border-radius: 4px;
    box-shadow: 0 18px 40px rgba(0,0,0,0.45);
    overflow: hidden;
  }
  .card--front { left: 50px; }
  .card--back { left: 630px; background: var(--card-white); color: var(--ink); }

  .front-photo {
    position: absolute; inset: 0;
    background:
      radial-gradient(ellipse at 65% 40%, var(--photo-mist) 0%, transparent 55%),
      linear-gradient(160deg, var(--photo-deep) 0%, var(--photo-mid) 55%, var(--photo-deep) 100%);
  }
  .wordmark {
    position: absolute;
    text-align: center;
    text-transform: uppercase;
    line-height: 1;
  }
  .wordmark__name { font-weight: 500; letter-spacing: 0.02em; }
  .wordmark__rule { display: block; height: 1px; margin: 6px auto 5px; }
  .wordmark__role { font-weight: 400; letter-spacing: 0.32em; }

  .card--front .wordmark {
    left: 0; right: 0; top: 138px;
    color: var(--on-photo);
  }
  .card--front .wordmark__name { font-size: 30px; }
  .card--front .wordmark__rule { width: 270px; background: var(--on-photo); }
  .card--front .wordmark__role { font-size: 11px; }

  .card--back .wordmark {
    left: 28px; width: 250px; top: 146px;
    color: var(--ink);
  }
  .card--back .wordmark__name { font-size: 23px; }
  .card--back .wordmark__rule { width: 230px; background: var(--ink); }
  .card--back .wordmark__role { font-size: 9.5px; }

  .divider {
    position: absolute;
    left: 296px; top: 78px;
    width: 1.5px; height: 180px;
    background: var(--rule);
  }
  .contact {
    position: absolute;
    left: 318px; top: 88px;
    font-size: 12.5px;
    line-height: 1.5;
    color: var(--ink-soft);
  }
  .contact__name {
    font-size: 15px; font-weight: 600;
    letter-spacing: 0.08em; text-transform: uppercase;
    color: var(--ink);
    line-height: 1.2;
  }
  .contact__role { margin-bottom: 8px; }
  .contact__address { font-style: normal; margin-bottom: 6px; }
  .contact__line { display: flex; align-items: center; gap: 7px; }
  .contact__line svg { width: 9px; height: 9px; flex: none; }
</style>
</head>
<body>

<section class="card card--front" aria-label="Vorderseite">
  <div class="front-photo" role="img" aria-label="Dunkles, nebliges Foto einer Person an einem Strand bei Dämmerung"></div>
  <div class="wordmark">
    <div class="wordmark__name">Tobias Lendhart</div>
    <span class="wordmark__rule"></span>
    <div class="wordmark__role">Personal Trainer</div>
  </div>
</section>

<section class="card card--back" aria-label="Rückseite">
  <div class="wordmark">
    <div class="wordmark__name">Tobias Lendhart</div>
    <span class="wordmark__rule"></span>
    <div class="wordmark__role">Personal Trainer</div>
  </div>

  <div class="divider"></div>

  <div class="contact">
    <div class="contact__name">Tobias Lendhart</div>
    <div class="contact__role">Personal Trainer</div>
    <address class="contact__address">Wiesengrundweg 14<br>80417 München</address>
    <div class="contact__line">
      <svg viewBox="0 0 10 10" aria-hidden="true"><path d="M2 0.5 L3.6 2.8 L2.8 3.8 Q3.8 6 6.2 7.2 L7.2 6.4 L9.5 8 L8.3 9.5 Q2.5 8.5 0.5 1.7 Z" fill="#333"/></svg>
      <span>0162/3819204</span>
    </div>
    <div class="contact__line">
      <svg viewBox="0 0 10 10" aria-hidden="true"><rect x="0.8" y="2" width="8.4" height="6" fill="none" stroke="#333" stroke-width="1"/><path d="M0.8 2 L5 5.4 L9.2 2" fill="none" stroke="#333" stroke-width="1"/></svg>
      <span>t.lendhart@postfach.de</span>
    </div>
    <div class="contact__line">
      <svg viewBox="0 0 10 10" aria-hidden="true"><circle cx="5" cy="5" r="4.2" fill="none" stroke="#333" stroke-width="1"/><ellipse cx="5" cy="5" rx="1.8" ry="4.2" fill="none" stroke="#333" stroke-width="0.8"/><path d="M0.8 5 H9.2" stroke="#333" stroke-width="0.8"/></svg>
      <span>www.tobiaslendhart.de</span>
    </div>
  </div>
</section>

</body>
</html>
```